Create a new business card

I’m looking to update my business card to make it match the rest of my brand. I will include my current website as well as what my vehicle designs look like, etc..
What my business currently services
Weekly maintenance pool openings / closings
Equipment repair, including pumps, heaters, salt systems, filters, etc.
We install automatic covers and maintain them as well as provide preventative maintenance

I would like to include my name.
Dorian Pelkin.
My title
Owner
My email
Dorian@tidewellnx.com
4015827160
Www.tidewellnx.com

```html
<!DOCTYPE html>
<html lang="en">
<head>
<meta charset="utf-8">
<title>Tidewell Pool Service – Business Card</title>
<link href="https://fonts.googleapis.com/css2?family=Poppins:wght@400;500;600&display=swap" rel="stylesheet">
<style>
  :root {
    --navy: #1e2f63;
    --sky: #27b1e4;
    --orange: #e8612c;
    --white: #ffffff;
    --stage: #1c1c1c;
  }
  * { margin: 0; padding: 0; box-sizing: border-box; }
  html, body { width: 1200px; height: 1200px; overflow: hidden; }
  body { background: var(--stage); font-family: "Poppins", sans-serif; position: relative; }

  .card {
    position: absolute; left: 250px; width: 700px; height: 400px;
    border-radius: 20px; overflow: hidden;
  }
  .card-front { top: 170px; background: var(--white); }
  .card-back { top: 630px; background: var(--sky); }
  .card-art { position: absolute; inset: 0; width: 700px; height: 400px; }

  .brand { position: absolute; display: flex; align-items: center; gap: 12px; }
  .brand-dot { width: 52px; height: 52px; border-radius: 50%; background: var(--sky); flex: none; }
  .brand-name { font-weight: 600; font-size: 22px; line-height: 1.15; }
  .card-front .brand { left: 60px; top: 110px; }
  .card-front .brand-name { color: var(--navy); }
  .card-back .brand { left: 445px; top: 165px; }
  .card-back .brand-name { color: var(--white); }

  .identity { position: absolute; right: 73px; top: 56px; text-align: right; }
  .person-name { font-weight: 600; font-size: 36px; color: var(--navy); line-height: 1.1; letter-spacing: 0.3px; }
  .person-title { font-size: 20px; color: var(--orange); line-height: 1.2; }

  .contact-list { position: absolute; right: 73px; top: 262px; list-style: none; }
  .contact-list li {
    display: flex; justify-content: flex-end; align-items: center; gap: 10px;
    color: var(--white); font-size: 19px; line-height: 29px;
  }
  .contact-list li.phone { font-size: 23px; font-weight: 500; }
  .contact-icon { width: 16px; height: 16px; flex: none; }

  .service-list { position: absolute; left: 34px; top: 68px; list-style: none; }
  .service-list li {
    display: flex; align-items: center; gap: 9px;
    color: var(--navy); font-size: 15.5px; line-height: 21.2px; letter-spacing: 0.4px;
  }
  .tick { width: 14px; height: 14px; flex: none; }
</style>
</head>
<body>

<section class="card card-front">
  <svg class="card-art" viewBox="0 0 700 400" aria-hidden="true">
    <path d="M0,190 C70,290 170,320 280,265 C390,210 500,170 580,178 C630,183 670,200 700,220 L700,400 L0,400 Z" fill="var(--navy)"/>
    <path d="M90,290 C180,330 270,300 360,255 C450,210 550,160 630,160" fill="none" stroke="var(--white)" stroke-width="5"/>
    <path d="M20,195 C90,280 200,300 323,230" fill="none" stroke="var(--orange)" stroke-width="5"/>
    <path d="M433,235 C520,195 620,185 690,225" fill="none" stroke="var(--sky)" stroke-width="6"/>
  </svg>

  <div class="brand">
    <span class="brand-dot"></span>
    <span class="brand-name">Tidewell<br>Pool Service</span>
  </div>

  <div class="identity">
    <h1 class="person-name">Dorian Pelkin</h1>
    <p class="person-title">Owner</p>
  </div>

  <ul class="contact-list">
    <li class="phone">(401) 582-7160
      <svg class="contact-icon" viewBox="0 0 16 16"><path d="M3 1.5l3 .5 1 3.5-2 1.3a9 9 0 0 0 4.2 4.2l1.3-2 3.5 1 .5 3c-.3 1.2-1.5 1.8-2.7 1.5A13 13 0 0 1 1.5 4.2C1.2 3 1.8 1.8 3 1.5z" fill="var(--orange)"/></svg>
    </li>
    <li>Dorian@tidewellnx.com
      <svg class="contact-icon" viewBox="0 0 16 16"><rect x="1" y="3" width="14" height="10" fill="var(--orange)"/><path d="M1.5 3.5L8 9l6.5-5.5" fill="none" stroke="var(--navy)" stroke-width="1.2"/></svg>
    </li>
    <li>tidewellnx.com
      <svg class="contact-icon" viewBox="0 0 16 16"><circle cx="8" cy="8" r="6.5" fill="none" stroke="var(--orange)" stroke-width="1.6"/><path d="M5 4c1.5 1 1 3 3 3.5s1 2.5-.5 3.5M10 3.5c0 1.5 1.5 1.5 3 2" fill="none" stroke="var(--orange)" stroke-width="1.6"/></svg>
    </li>
  </ul>
</section>

<section class="card card-back">
  <svg class="card-art" viewBox="0 0 700 400" aria-hidden="true">
    <path d="M387,0 C310,50 300,140 330,210 C355,270 375,330 370,400 L700,400 L700,0 Z" fill="var(--navy)"/>
    <path d="M378,0 C300,55 290,140 320,210 C345,270 365,330 360,400" fill="none" stroke="var(--sky)" stroke-width="5"/>
    <path d="M383,12 C330,50 315,110 348,190" fill="none" stroke="var(--orange)" stroke-width="5"/>
  </svg>

  <ul class="service-list">
    <li><svg class="tick" viewBox="0 0 14 14"><circle cx="7" cy="7" r="7" fill="var(--navy)"/><path d="M4 7.2l2 2 4-4" fill="none" stroke="var(--sky)" stroke-width="1.8"/></svg>Weekly Pool Maintenance</li>
    <li><svg class="tick" viewBox="0 0 14 14"><circle cx="7" cy="7" r="7" fill="var(--navy)"/><path d="M4 7.2l2 2 4-4" fill="none" stroke="var(--sky)" stroke-width="1.8"/></svg>Pool Opening &amp; Closing</li>
    <li><svg class="tick" viewBox="0 0 14 14"><circle cx="7" cy="7" r="7" fill="var(--navy)"/><path d="M4 7.2l2 2 4-4" fill="none" stroke="var(--sky)" stroke-width="1.8"/></svg>Equipment Servicing</li>
    <li><svg class="tick" viewBox="0 0 14 14"><circle cx="7" cy="7" r="7" fill="var(--navy)"/><path d="M4 7.2l2 2 4-4" fill="none" stroke="var(--sky)" stroke-width="1.8"/></svg>Equipment Installation</li>
    <li><svg class="tick" viewBox="0 0 14 14"><circle cx="7" cy="7" r="7" fill="var(--navy)"/><path d="M4 7.2l2 2 4-4" fill="none" stroke="var(--sky)" stroke-width="1.8"/></svg>Structural Pool Repair</li>
    <li><svg class="tick" viewBox="0 0 14 14"><circle cx="7" cy="7" r="7" fill="var(--navy)"/><path d="M4 7.2l2 2 4-4" fill="none" stroke="var(--sky)" stroke-width="1.8"/></svg>Plumbing Updates &amp; Upgrades</li>
    <li><svg class="tick" viewBox="0 0 14 14"><circle cx="7" cy="7" r="7" fill="var(--navy)"/><path d="M4 7.2l2 2 4-4" fill="none" stroke="var(--sky)" stroke-width="1.8"/></svg>Coping Replacement &amp; Removal</li>
    <li><svg class="tick" viewBox="0 0 14 14"><circle cx="7" cy="7" r="7" fill="var(--navy)"/><path d="M4 7.2l2 2 4-4" fill="none" stroke="var(--sky)" stroke-width="1.8"/></svg>Tile Replacement &amp; Removal</li>
    <li><svg class="tick" viewBox="0 0 14 14"><circle cx="7" cy="7" r="7" fill="var(--navy)"/><path d="M4 7.2l2 2 4-4" fill="none" stroke="var(--sky)" stroke-width="1.8"/></svg>Interior Resurfacing/Replastering</li>
    <li><svg class="tick" viewBox="0 0 14 14"><circle cx="7" cy="7" r="7" fill="var(--navy)"/><path d="M4 7.2l2 2 4-4" fill="none" stroke="var(--sky)" stroke-width="1.8"/></svg>Filter System Equipment Upgrades</li>
    <li><svg class="tick" viewBox="0 0 14 14"><circle cx="7" cy="7" r="7" fill="var(--navy)"/><path d="M4 7.2l2 2 4-4" fill="none" stroke="var(--sky)" stroke-width="1.8"/></svg>Decking Removal &amp; Renovation</li>
    <li><svg class="tick" viewBox="0 0 14 14"><circle cx="7" cy="7" r="7" fill="var(--navy)"/><path d="M4 7.2l2 2 4-4" fill="none" stroke="var(--sky)" stroke-width="1.8"/></svg>Commercial Pool Services</li>
  </ul>

  <div class="brand">
    <span class="brand-dot"></span>
    <span class="brand-name">Tidewell<br>Pool Service</span>
  </div>
</section>

</body>
</html>
```